Window Treatment business needs website redesigned.

We need a revamp and refresh of our current site www.velmarix.ca
Looking to attract very high end customer. It should be a very simple design with very little text. This site will be visited by prospective homeowners, designers, builders and architects. They should feel that they are dealing with a high-end product selection, where experience, customer service and unique product offering is the focus. The content will be to highlight our services and highlight the manufacturers we sell, using a few rich photos to highlight the products. We should NOT look like we are a very large company. It should NOT have discounts/savings buttons and many menus to choose from. We offer over 15 years experience to narrow the many market options, to provide the right technical solution.
We specialize in products that are not readily available on the market and specifically motorized systems for indoors and outdoors.
Our main suppliers are Kravenholt.com, Dimbrell.com
We carry our own locally manufactured product line of roller shades.
Main product pictures should be of roller shades, outdoor bug screens, awnings and outdoor pergolas.

Reason: I understand that Christmas is coming up real short and many people are extremely busy. If you have a CREATIVE gifting you still want to submit, I look forward to your idea!

Reason: Due to holiday season, we have not had sufficient time to review to make a final decision. Thank you for your patience!

Target Market(s)

High end home owners, designers, builders, architects

Industry/Entity Type

Contractor

Coding

Coded - Design and coding required

Number of Pages Required

3 page

Font styles to use
Sans Serif

Requirements
Must have
• Landing page with full size image like homepage of zolvane.it
• Products page that highlights products with simple product shot image, description and link to manufacturer.
• On main page a scrolling of customer reviews.
• I want a very simple, eye-catching, emotional image for homepage. It does not need to include any product image.
• An image that shows technology combining/meshing with hand craftsmanship.
• Focus is on design.
• http://www.zolvane.it/en/gallery is a great layout and design.
Nice to have
• Logo shape for icons and watermark should be used.
• Look like and have simple motion effects like quorix.com or telvarin.com
Should not have
• Generic/standard looking feel like bluppet.com or mecklorwindow.ca
• No use of green as background only subtle text.
• Lots of text and pages.

```html
<!DOCTYPE html>
<html lang="en">
<head>
<meta charset="utf-8">
<title>Velmarix — Motorized Shades</title>
<link rel="stylesheet" href="https://fonts.googleapis.com/css2?family=Open+Sans:ital,wght@0,400;0,600;0,700;1,400&display=swap">
<style>
  :root {
    --white: #ffffff;
    --green: #7ab648;
    --green-text: #8cc152;
    --tile-fill: rgba(24, 26, 28, 0.55);
    --overlay: rgba(20, 22, 24, 0.45);
    --sky-top: #3f6f9f;
    --sky-mid: #8aa9c4;
    --hills: #4d6a3a;
    --hills-dark: #33472a;
    --rule: rgba(255, 255, 255, 0.55);
    --dot: rgba(255, 255, 255, 0.5);
  }
  * { box-sizing: border-box; margin: 0; padding: 0; }
  html, body { width: 1200px; height: 738px; overflow: hidden; background: #222; }
  body { font-family: "Open Sans", Arial, sans-serif; color: var(--white); }

  .page { position: relative; width: 1200px; height: 738px; overflow: hidden; }

  .hero-photo {
    position: absolute; inset: 0;
    background:
      linear-gradient(200deg, #4a4946 0%, #5b5955 30%, rgba(90,88,84,0) 48%),
      linear-gradient(180deg, var(--sky-top) 0%, var(--sky-mid) 45%, #9fb3c0 55%, var(--hills) 66%, var(--hills-dark) 100%);
  }
  .hero-overlay { position: absolute; inset: 0; background: var(--overlay); }

  .site-header { position: absolute; top: 33px; left: 75px; right: 73px; height: 72px; display: flex; align-items: center; justify-content: space-between; }
  .brand { display: flex; align-items: center; gap: 12px; }
  .brand-mark { width: 70px; height: 70px; border: 4px solid var(--white); border-radius: 50%; }
  .brand-name { font-size: 38px; font-weight: 400; letter-spacing: 0.5px; }

  .main-nav { display: flex; align-items: center; gap: 4px; }
  .main-nav a { color: var(--white); text-decoration: none; font-size: 13.5px; font-weight: 700; letter-spacing: 0.3px; padding: 6px 16px; border: 2px solid transparent; border-radius: 18px; }
  .main-nav a.is-active { border-color: var(--green); padding: 6px 22px; }
  .main-nav a:last-child { padding-right: 0; }

  .hero-copy { position: absolute; left: 76px; top: 180px; }
  .hero-title { font-size: 50px; font-weight: 700; letter-spacing: 2px; line-height: 1.1; }
  .hero-lead { margin-top: 15px; font-size: 20px; font-weight: 600; line-height: 29px; letter-spacing: 0.4px; width: 470px; }

  .reviews { position: absolute; left: 75px; top: 474px; width: 426px; }
  .reviews-head { display: flex; justify-content: space-between; align-items: center; }
  .reviews-title { font-size: 16.5px; font-weight: 600; letter-spacing: 0.4px; }
  .reviews-arrows { display: flex; gap: 10px; }
  .reviews-arrows svg { width: 12px; height: 16px; }
  .review-quote { margin-top: 24px; width: 426px; font-size: 15.5px; font-style: italic; line-height: 24px; }
  .review-author { margin-top: 9px; font-size: 14px; font-weight: 700; color: var(--green-text); }
  .review-dots { margin-top: 22px; display: flex; gap: 9px; }
  .review-dots span { width: 8px; height: 8px; border-radius: 50%; background: var(--dot); }
  .review-dots span.is-current { background: var(--white); }

  .tiles { position: absolute; left: 790px; top: 238px; width: 340px; height: 340px; }
  .tile { position: absolute; width: 166px; height: 166px; display: flex; flex-direction: column; align-items: center; justify-content: center; gap: 14px; color: var(--white); text-decoration: none; }
  .tile > svg.tile-shape { position: absolute; inset: 0; width: 100%; height: 100%; }
  .tile-icon, .tile-label { position: relative; }
  .tile-icon { width: 38px; height: 36px; }
  .tile-label { font-size: 17px; font-weight: 700; letter-spacing: 0.6px; }
  .tile--about { left: 2px; top: 2px; }
  .tile--products { left: 171px; top: 2px; }
  .tile--suppliers { left: 2px; top: 171px; }
  .tile--gallery { left: 171px; top: 171px; }
  .tiles-badge { position: absolute; left: 141px; top: 142px; width: 54px; height: 54px; border-radius: 50%; border: 4px solid var(--white); background: rgba(30,30,30,0.5); }

  .site-footer { position: absolute; left: 0; right: 0; top: 674px; height: 64px; border-top: 1px solid var(--rule); }
  .copyright { position: absolute; left: 75px; top: 26px; font-size: 12.5px; }
  .social { position: absolute; right: 74px; top: 21px; display: flex; gap: 22px; }
  .social span { width: 22px; height: 22px; border-radius: 3px; background: var(--white); }
</style>
</head>
<body>
<div class="page">
  <div class="hero-photo" role="img" aria-label="Photo of an outdoor pergola with retractable motorized shade roof overlooking green mountain slopes under a blue sky"></div>
  <div class="hero-overlay"></div>

  <header class="site-header">
    <div class="brand">
      <span class="brand-mark"></span>
      <span class="brand-name">Velmarix</span>
    </div>
    <nav class="main-nav">
      <a href="#" class="is-active">HOME</a>
      <a href="#">ABOUT US</a>
      <a href="#">SERVICES</a>
      <a href="#">GALLERY</a>
      <a href="#">REVIEWS</a>
      <a href="#">CONTACT US</a>
    </nav>
  </header>

  <section class="hero-copy">
    <h1 class="hero-title">MOTORIZED SHADES</h1>
    <p class="hero-lead">We offer both top-of-the-line and affordable automated blinds.</p>
  </section>

  <section class="reviews">
    <div class="reviews-head">
      <h2 class="reviews-title">CUSTOMER REVIEWS</h2>
      <div class="reviews-arrows">
        <svg viewBox="0 0 12 16"><path d="M9 2 L3 8 L9 14" fill="none" stroke="#fff" stroke-width="2.5"/></svg>
        <svg viewBox="0 0 12 16"><path d="M3 2 L9 8 L3 14" fill="none" stroke="#fff" stroke-width="2.5"/></svg>
      </div>
    </div>
    <blockquote class="review-quote">“&nbsp; Aliquam molestie, mi et imperdiet euismod, dui purus<br>auctor tellus, et interdum lacus lectus et ante egestas risus in<br>magna varius nibh eget turpis vehicula tempus..”</blockquote>
    <p class="review-author">-Name Heading</p>
    <div class="review-dots"><span class="is-current"></span><span></span><span></span><span></span></div>
  </section>

  <nav class="tiles">
    <a href="#" class="tile tile--about">
      <svg class="tile-shape" viewBox="-83 -83 166 166"><polygon points="75,31 31,75 -31,75 -75,31 -75,-31 -31,-75 31,-75 75,-31" fill="var(--tile-fill)" stroke="#fff" stroke-width="3"/></svg>
      <svg class="tile-icon" viewBox="0 0 38 36"><circle cx="19" cy="10" r="8" fill="#fff"/><path d="M4 35 Q4 20 19 20 Q34 20 34 35 Z" fill="#fff"/></svg>
      <span class="tile-label">ABOUT US</span>
    </a>
    <a href="#" class="tile tile--products">
      <svg class="tile-shape" viewBox="-83 -83 166 166"><polygon points="75,31 31,75 -31,75 -75,31 -75,-31 -31,-75 31,-75 75,-31" fill="var(--tile-fill)" stroke="#fff" stroke-width="3"/></svg>
      <svg class="tile-icon" viewBox="0 0 38 36"><rect x="6" y="6" width="26" height="20" rx="2" fill="none" stroke="#fff" stroke-width="3"/><path d="M1 29 H37 L35 33 H3 Z" fill="#fff"/></svg>
      <span class="tile-label">PRODUCTS</span>
    </a>
    <a href="#" class="tile tile--suppliers">
      <svg class="tile-shape" viewBox="-83 -83 166 166"><polygon points="75,31 31,75 -31,75 -75,31 -75,-31 -31,-75 31,-75 75,-31" fill="var(--tile-fill)" stroke="#fff" stroke-width="3"/></svg>
      <svg class="tile-icon" viewBox="0 0 38 36"><circle cx="8" cy="10" r="5" fill="#fff"/><circle cx="30" cy="10" r="5" fill="#fff"/><circle cx="19" cy="8" r="6.5" fill="#fff"/><path d="M0 28 Q0 17 8 17 Q14 17 14 24 V28 Z" fill="#fff"/><path d="M38 28 Q38 17 30 17 Q24 17 24 24 V28 Z" fill="#fff"/><path d="M9 35 Q9 17 19 17 Q29 17 29 35 Z" fill="#fff"/></svg>
      <span class="tile-label">SUPPLIERS</span>
    </a>
    <a href="#" class="tile tile--gallery">
      <svg class="tile-shape" viewBox="-83 -83 166 166"><polygon points="75,31 31,75 -31,75 -75,31 -75,-31 -31,-75 31,-75 75,-31" fill="var(--tile-fill)" stroke="#fff" stroke-width="3"/></svg>
      <svg class="tile-icon" viewBox="0 0 38 36"><rect x="2" y="3" width="34" height="30" fill="none" stroke="#fff" stroke-width="3"/><circle cx="11" cy="12" r="3.5" fill="#fff"/><path d="M6 29 L15 19 L20 24 L27 14 L32 29 Z" fill="#fff"/></svg>
      <span class="tile-label">GALLERY</span>
    </a>
    <span class="tiles-badge"></span>
  </nav>

  <footer class="site-footer">
    <p class="copyright">Copyright © 2016. Company Name. All Right Reserved</p>
    <div class="social"><span></span><span></span><span></span><span></span><span></span></div>
  </footer>
</div>
</body>
</html>
```